Automotive component supplier needs a business card design

We need a business card design for our company called Velran Global Components Ltd based in the UK. We are a supplier of interior and exterior components to premium car manufacturers such as Corvel Ashby, Hadley Fenn, Marquist and Tavarelli. We would like to see a modern business card design that uses the colour blue.

Target Market(s)

Premium automotive car manufacturers.

Industry/Entity Type

Automotive

Contact Information for Business Card

Company Name : Velran Global Components Limited
Address: 17 Marlow Yard, Upper Heath, Warwick, CV31 8QL, United Kingdom
Web Address : www.velrancomponents-example.co.uk

Font styles to use
Other font styles liked:
• Helvetica

Colors
3176b5
0255a3
85acd3
cfdeed
cee9f5
85cae6
34a6d7
0692cd
9bcb3c

Requirements
Must have
• Clear company logo and a mixture of blue colours.
Nice to have
• A high quality modern image.
Should not have
• Multiple colours.

```html
<!DOCTYPE html>
<html lang="en">
<head>
<meta charset="utf-8">
<title>Velran Global Components – Business Card</title>
<link href="https://fonts.googleapis.com/css2?family=Michroma&family=Arimo:wght@400&display=swap" rel="stylesheet">
<style>
  :root{
    --backdrop:#4a3526;
    --card:#050608;
    --blue:#1a8fd0;
    --green:#9bcb3c;
  }
  html,body{margin:0;padding:0;overflow:hidden}
  body{width:1200px;height:843px;background:var(--backdrop);position:relative;font-family:"Arimo",Helvetica,Arial,sans-serif}
  .card{position:absolute;top:252px;width:558px;height:319px;background:var(--card);border-radius:16px;box-shadow:0 4px 10px rgba(0,0,0,.45)}
  .card--front{left:28px}
  .card--back{left:614px}
  .brand{position:absolute;color:var(--blue);font-family:"Michroma",sans-serif;font-weight:400;white-space:nowrap;line-height:1}
  .brand__name{font-size:29px;letter-spacing:1px;display:flex;align-items:center;gap:8px}
  .brand__mark{width:9px;height:9px;background:var(--blue);display:inline-block}
  .brand__line{font-size:10.6px;letter-spacing:.6px;margin-top:9px}
  .card--front .brand{left:23px;top:56px}
  .card--back .brand{right:25px;top:132px;text-align:right}
  .card--back .brand__name{justify-content:flex-end}
  .person{position:absolute;left:25px;top:121px}
  .person__name{font-family:"Michroma",sans-serif;color:var(--blue);font-size:15.5px;letter-spacing:1px;margin:0}
  .person__role{color:var(--green);font-size:14px;margin:4px 0 0}
  .address{position:absolute;left:25px;top:164px;color:var(--blue);font-size:14px;line-height:18px;margin:0;font-style:normal}
  .contacts{position:absolute;left:25px;top:206px;list-style:none;margin:0;padding:0;color:var(--blue);font-size:13.8px;line-height:17.7px}
  .contacts li{display:flex;align-items:center;gap:8px}
  .contacts svg{width:11px;height:11px;flex:none}
  .web{position:absolute;right:25px;bottom:14px;color:var(--blue);font-size:13.8px}
</style>
</head>
<body>
  <section class="card card--front">
    <div class="brand">
      <div class="brand__name"><span>VELRAN</span><span class="brand__mark"></span></div>
      <div class="brand__line">GLOBAL COMPONENTS</div>
    </div>
    <div class="person">
      <p class="person__name">NEIL HARTIGAN</p>
      <p class="person__role">Director</p>
    </div>
    <address class="address">17 Marlow Yard, Upper Heath<br>Warwick, CV31 8QL, UK</address>
    <ul class="contacts">
      <li><svg viewBox="0 0 12 12"><path d="M3 1l2 2-1 1.5c.6 1.4 1.6 2.4 3 3L8.5 6.5l2 2-1.5 2C5 10 2 7 1.5 2.5z" fill="var(--green)"/></svg>780 555-0142</li>
      <li><svg viewBox="0 0 12 12"><rect x="3.5" y="1" width="5" height="10" rx="1" fill="none" stroke="var(--green)" stroke-width="1.2"/></svg>780 555-0187</li>
      <li><svg viewBox="0 0 12 12"><rect x="1" y="3" width="10" height="6.5" fill="var(--green)"/><path d="M1 3l5 3.5L11 3" fill="none" stroke="var(--card)" stroke-width="1"/></svg>velranparts@example.com</li>
      <li><svg viewBox="0 0 12 12"><g fill="none" stroke="var(--green)" stroke-width="1"><circle cx="6" cy="6" r="4.5"/><ellipse cx="6" cy="6" rx="2" ry="4.5"/><path d="M1.5 6h9"/></g></svg>www.velrancomponents-example.co.uk</li>
    </ul>
  </section>

  <section class="card card--back">
    <div class="brand">
      <div class="brand__name"><span>VELRAN</span><span class="brand__mark"></span></div>
      <div class="brand__line">GLOBAL COMPONENTS</div>
    </div>
    <div class="web">www.velrancomponents-example.co.uk</div>
  </section>
</body>
</html>
```